Corporate Business Card

Very professional, Modern, Not to busy, include phone address email, website
(360) 617-4930, 18761 52nd Avenue S, Alder Falls, OR 98047, martin@plumlinegroup.com, varkoworks.com

Target Market(s)

Manufacturing

Industry/Entity Type

Aero, machining, manufacturing, Off road racing

Contact Information for Business Card

Phone, address email, website

```html
<!DOCTYPE html>
<html lang="en">
<head>
<meta charset="utf-8">
<title>Varko Works – Business Card</title>
<link href="https://fonts.googleapis.com/css2?family=Arimo:wght@400;700&display=swap" rel="stylesheet">
<style>
  :root {
    --page-bg: #e4e4e2;
    --card-navy: #22356b;
    --brand-red: #cc1a1f;
    --ink-white: #ffffff;
  }
  * { box-sizing: border-box; margin: 0; padding: 0; }
  html, body {
    width: 1200px; height: 801px; overflow: hidden;
    background: var(--page-bg);
    font-family: "Arimo", Arial, sans-serif;
  }
  .stage {
    position: relative; width: 1200px; height: 801px;
    display: flex; align-items: center; justify-content: center; gap: 40px;
  }
  .card {
    position: relative; width: 540px; height: 309px;
    background: var(--card-navy); color: var(--ink-white);
  }
  .brand-name {
    position: absolute; font-weight: 700; color: var(--ink-white);
    letter-spacing: 1px; line-height: 1; white-space: nowrap;
  }
  .brand-rule { position: absolute; height: 2px; background: var(--ink-white); }

  /* front */
  .card-front .brand-name { left: 40px; top: 44px; font-size: 46px; }
  .card-front .brand-rule { left: 40px; top: 110px; width: 200px; }
  .identity { position: absolute; left: 40px; top: 138px; }
  .person-name { color: var(--brand-red); font-size: 20px; letter-spacing: 0.5px; }
  .person-role { font-size: 15px; margin-top: 4px; text-align: right; }
  .divider { position: absolute; left: 262px; top: 130px; width: 1px; height: 62px; background: var(--ink-white); }
  .contact-list { position: absolute; left: 280px; top: 126px; list-style: none; }
  .contact-list li { display: flex; align-items: center; gap: 9px; font-size: 13.5px; line-height: 23px; }
  .contact-list svg { width: 13px; height: 13px; flex: none; }
  .address { position: absolute; left: 40px; bottom: 36px; font-size: 15px; letter-spacing: 0.3px; }

  /* back */
  .card-back .brand-name { left: 0; right: 0; top: 118px; text-align: center; font-size: 54px; }
  .card-back .brand-rule { left: 110px; top: 190px; width: 170px; }
</style>
</head>
<body>
<main class="stage">
  <section class="card card-front">
    <div class="brand-name">VARKO WORKS</div>
    <div class="brand-rule"></div>
    <div class="identity">
      <p class="person-name">DANIEL REYES</p>
      <p class="person-role">Manager</p>
    </div>
    <div class="divider"></div>
    <ul class="contact-list">
      <li>
        <svg viewBox="0 0 16 16" aria-hidden="true"><path fill="#cc1a1f" d="M3.6 1.5l2.3 2.8-1.4 1.6c.9 2 2.4 3.5 4.4 4.4l1.6-1.4 2.8 2.3-1.3 2.3C6.9 14.7 1.3 9.1 1.3 2.8z"/></svg>
        (360) 617-4930
      </li>
      <li>
        <svg viewBox="0 0 16 16" aria-hidden="true"><rect x="1" y="3" width="14" height="10" fill="#cc1a1f"/><path d="M1.5 3.5L8 9l6.5-5.5" fill="none" stroke="#22356b" stroke-width="1.3"/></svg>
        martin@plumlinegroup.com
      </li>
      <li>
        <svg viewBox="0 0 16 16" aria-hidden="true"><circle cx="8" cy="8" r="6.5" fill="none" stroke="#cc1a1f" stroke-width="1.6"/><ellipse cx="8" cy="8" rx="2.6" ry="6.5" fill="none" stroke="#cc1a1f" stroke-width="1.3"/><path d="M1.5 8h13" stroke="#cc1a1f" stroke-width="1.3"/></svg>
        www.varkoworks.com
      </li>
    </ul>
    <p class="address">18761 52nd Avenue S, Alder Falls, OR 98047</p>
  </section>

  <section class="card card-back">
    <div class="brand-name">VARKO WORKS</div>
    <div class="brand-rule"></div>
  </section>
</main>
</body>
</html>
```